Veldmark Supplies Business Card

Professional business card that stand out to our potential customers. Front and back with clean modern design

Industry/Entity Type

Oil and gas

Contact Information for Business Card

Name, address, website , office phone and cell number

Requirements
Must have
• Editable files for each employee

```html
<!DOCTYPE html>
<html lang="en">
<head>
<meta charset="utf-8">
<title>Veldmark Supplies Business Card</title>
<link rel="stylesheet" href="https://fonts.googleapis.com/css2?family=Montserrat:wght@400;500;800&display=swap">
<style>
  :root {
    --backdrop: #4b4b4a;
    --card: #171717;
    --edge: #0aa9cc;
    --red: #ed1f24;
    --cyan: #05acd0;
    --white: #f2f2f2;
    --grey: #8e8e8e;
  }
  * { box-sizing: border-box; margin: 0; padding: 0; }
  html, body { width: 1200px; height: 801px; overflow: hidden; }
  body {
    background: var(--backdrop);
    font-family: "Montserrat", sans-serif;
    display: flex;
    align-items: center;
    justify-content: center;
    gap: 50px;
  }
  .card {
    width: 525px;
    height: 300px;
    background: var(--card);
    border-radius: 14px;
    border-bottom: 3px solid var(--edge);
    border-right: 3px solid var(--edge);
    position: relative;
    overflow: hidden;
  }
  /* front */
  .brand {
    position: absolute;
    left: 34px;
    top: 0;
    width: 200px;
    height: 100%;
    display: flex;
    align-items: center;
    gap: 10px;
  }
  .brand-mark { width: 14px; height: 14px; background: var(--red); flex: none; }
  .brand-name {
    font-weight: 800;
    font-size: 19px;
    color: var(--red);
    text-transform: uppercase;
    letter-spacing: 0.5px;
    line-height: 1.15;
  }
  .divider {
    position: absolute;
    left: 250px;
    top: 40px;
    bottom: 40px;
    width: 1.5px;
    background: var(--red);
  }
  .details {
    position: absolute;
    left: 275px;
    top: 42px;
    color: var(--white);
  }
  .person-name {
    font-weight: 800;
    font-size: 22px;
    text-transform: uppercase;
    letter-spacing: 0.5px;
  }
  .person-name .first { color: var(--red); }
  .person-name .last { color: var(--cyan); }
  .person-role { font-size: 12.5px; margin: 4px 0 14px; }
  .address { font-size: 12px; line-height: 1.55; margin-bottom: 12px; }
  .contacts { list-style: none; font-size: 12px; line-height: 1.75; }
  .contacts li { display: flex; align-items: center; gap: 8px; }
  .contacts svg { width: 12px; height: 12px; flex: none; fill: none; stroke: var(--red); stroke-width: 2; }
  .contacts svg.solid { fill: var(--red); stroke: none; }
  /* back */
  .card-back { display: flex; align-items: center; justify-content: center; gap: 14px; }
  .card-back .brand-mark { width: 22px; height: 22px; background: var(--grey); }
  .card-back .brand-name { font-size: 30px; color: var(--grey); }
</style>
</head>
<body>
  <section class="card card-front">
    <div class="brand">
      <span class="brand-mark"></span>
      <span class="brand-name">Veldmark Supplies</span>
    </div>
    <div class="divider"></div>
    <div class="details">
      <h1 class="person-name"><span class="first">Daniel</span> <span class="last">Hartley</span></h1>
      <p class="person-role">Managing Director</p>
      <p class="address">415 N.Ridgeline Suite 7<br>Larkfield, Tx 79188</p>
      <ul class="contacts">
        <li><svg class="solid" viewBox="0 0 24 24"><path d="M6.6 10.8a15 15 0 0 0 6.6 6.6l2.2-2.2a1 1 0 0 1 1-.25 11.4 11.4 0 0 0 3.6.57 1 1 0 0 1 1 1V20a1 1 0 0 1-1 1A17 17 0 0 1 3 4a1 1 0 0 1 1-1h3.5a1 1 0 0 1 1 1c0 1.25.2 2.45.57 3.57a1 1 0 0 1-.25 1z"/></svg>(555)210-0384</li>
        <li><svg viewBox="0 0 24 24"><rect x="6" y="2" width="12" height="20" rx="2"/><path d="M11 18h2"/></svg>555 318 642</li>
        <li><svg viewBox="0 0 24 24"><rect x="2" y="5" width="20" height="14"/><path d="M2 5l10 8 10-8"/></svg>sales@veldmarksupplies.com</li>
        <li><svg viewBox="0 0 24 24"><circle cx="12" cy="12" r="10"/><path d="M2 12h20M12 2a15 15 0 0 1 0 20M12 2a15 15 0 0 0 0 20"/></svg>www.veldmarksupplies.com</li>
      </ul>
    </div>
  </section>
  <section class="card card-back">
    <span class="brand-mark"></span>
    <span class="brand-name">Veldmark Supplies</span>
  </section>
</body>
</html>
```